R7M Horizon Business Card Design

We need a business card created for our New Business "R7M Horizon"<br/><br/>The business card design is up to you however the following information must be on the business card:<br/><br/>Front of the business card -<br/>Email :darrenp@r7mhorizon.nz<br/>Mobile: +64 (0) 22 4870 619<br/>Website: www.r7mhorizon.nz<br/>Card Owner Name: Darren Paltrow<br/>Company Title: Business Development Manager<br/>Slogan: "The BEST of both worlds". <br/>Logo On the front attached to the design brief<br/><br/>On the back: <br/>Space on the back for 4 more versions of the logo across the bottom of the card indicating different subsidiary brands - R7M Coffee, R7M Arts, R7M ?? (The card will be used for all of these brands - We Will add the extra subsidiary logos to the design once the design is finished (We are a graphics design team). <br/><br/>Other than that we want a premium feeling logo that remains universally usable depending on the business entity that we are using the card for. The use of bright bold colours would be great but we still want the card to feel premium.
Target Market(s)
Gift Design and Manufacturing Companies
Contact Information for Business Card
Front of the business card -
Email :darrenp@r7mhorizon.nz
Mobile: +64 (0) 22 4870 619
Website: www.r7mhorizon.nz
Card Owner Name: Darren Paltrow
Company Title: Business Development Manager
Slogan: "The BEST of both worlds".
Logo On the front attached to the design brief

```html
<!DOCTYPE html>
<html lang="en">
<head>
<meta charset="utf-8">
<title>R7M Horizon – Business Card</title>
<link href="https://fonts.googleapis.com/css2?family=Exo+2:wght@400;500;700&display=swap" rel="stylesheet">
<style>
  :root {
    --backdrop: #2a2b2e;
    --card-dark: #1d1e21;
    --card-light: #ffffff;
    --brand-blue: #3546a0;
    --ink-dark: #2b2b2e;
    --faint-ring: #262a3c;
    --faint-name: #2d2f35;
    --white: #ffffff;
  }
  * { margin: 0; padding: 0; box-sizing: border-box; }
  html, body {
    width: 1200px; height: 900px; overflow: hidden;
    background: var(--backdrop);
    font-family: "Exo 2", sans-serif;
  }
  .stage {
    position: relative; width: 1200px; height: 900px;
  }
  .card {
    position: absolute; left: 280px;
    width: 640px; height: 366px;
    overflow: hidden;
  }
  /* Back */
  .card-back {
    top: 54px;
    background: var(--card-dark);
    border-left: 3px solid var(--brand-blue);
    border-bottom: 3px solid var(--brand-blue);
  }
  .back-ring {
    position: absolute; left: 50%; top: 50%;
    width: 300px; height: 300px; margin: -150px 0 0 -150px;
    border: 5px solid var(--faint-ring); border-radius: 50%;
  }
  .back-name {
    position: absolute; inset: 0;
    display: flex; align-items: center; justify-content: center;
    font-weight: 700; font-size: 40px; color: var(--faint-name);
    letter-spacing: 1px;
  }
  /* Front */
  .card-front {
    top: 462px;
    background: var(--card-light);
    border-left: 3px solid var(--brand-blue);
    border-bottom: 3px solid var(--brand-blue);
  }
  .front-brand {
    position: absolute; left: 40px; top: 150px;
    font-weight: 700; font-size: 38px; color: var(--brand-blue);
    letter-spacing: 0.5px;
  }
  .holder {
    position: absolute; left: 392px; top: 78px;
  }
  .holder-name {
    font-weight: 700; font-size: 24px; color: var(--brand-blue);
    letter-spacing: 1px; text-transform: uppercase; line-height: 1.1;
  }
  .holder-title {
    font-weight: 400; font-size: 15px; color: var(--ink-dark);
  }
  .contact-band {
    position: absolute; left: 345px; right: 0; top: 158px; height: 118px;
    background: var(--brand-blue);
    border-radius: 59px 0 0 59px;
    padding: 20px 0 0 40px;
    list-style: none;
  }
  .contact-item {
    display: flex; align-items: center; gap: 10px;
    color: var(--white); font-size: 17px; font-weight: 500;
    letter-spacing: 0.6px; line-height: 26px;
  }
  .contact-item svg { width: 16px; height: 16px; flex: none; }
  .slogan {
    position: absolute; left: 352px; top: 318px;
    font-size: 19px; font-weight: 400; color: var(--brand-blue);
    text-transform: uppercase; letter-spacing: 0.4px;
  }
</style>
</head>
<body>
<main class="stage">
  <section class="card card-back" aria-label="Card back">
    <div class="back-ring"></div>
    <div class="back-name">R7M Horizon</div>
  </section>

  <section class="card card-front" aria-label="Card front">
    <div class="front-brand">R7M Horizon</div>

    <div class="holder">
      <h1 class="holder-name">Darren Paltrow</h1>
      <p class="holder-title">Business Development Manager</p>
    </div>

    <ul class="contact-band">
      <li class="contact-item">
        <svg viewBox="0 0 16 16" fill="none" stroke="#fff" stroke-width="1.3"><circle cx="8" cy="8" r="6.5"/><path d="M5.5 4.8l1.2 1.6-.7 1c.5 1 1.3 1.8 2.3 2.3l1-.7 1.6 1.2-.8 1.1c-2.6-.4-4.8-2.6-5.2-5.2z" fill="#fff" stroke="none"/></svg>
        +64 (0) 22 4870 619
      </li>
      <li class="contact-item">
        <svg viewBox="0 0 16 16" fill="none" stroke="#fff" stroke-width="1.3"><rect x="1.5" y="3.5" width="13" height="9"/><path d="M1.5 3.5l6.5 5 6.5-5"/></svg>
        darrenp@r7mhorizon.nz
      </li>
      <li class="contact-item">
        <svg viewBox="0 0 16 16" fill="none" stroke="#fff" stroke-width="1.2"><circle cx="8" cy="8" r="6.5"/><ellipse cx="8" cy="8" rx="3" ry="6.5"/><path d="M1.5 8h13M2.5 4.8h11M2.5 11.2h11"/></svg>
        www.r7mhorizon.nz
      </li>
    </ul>

    <p class="slogan">The Best of Both Worlds</p>
  </section>
</main>
</body>
</html>
```